High-end Oceanfront Real Estate Group Needs Clean, Modern Web Design

I’m looking for a clean, professional, modern and beautiful homepage web design for a Real Estate group in Southern California, USA.

The group/company is “Marwick on the Shore,” and they specialize in high end (i.e. expensive), oceanfront real estate in the Orange County area.

The look and feel of the page should accentuate the brand qualities: luxurious/expensive, professional, and beautiful (Orange County is one of the most beautiful areas in all the US and we would love the site to emphasize the beautiful beaches and scenery it has to offer).

Looks we like:
• www.brantleyhomesrealty.example
• www.closedbyvane.example -- I think the design is pretty out-dated in this site, but I like the organization/layout of the site

Header Tags (I don’t know if we can fit all of these, may need a side-menu, but I’d prefer header title only if possible):
• Welcome
• Featured Listings
• Previously Sold
• Sell
• Property Search
• Team
• Videos
• Blog
• Explore O.C.
• Contact

I have attached the beach and logo pics that we would like to use as the header, a few pictures of the team, and one sample home/view pic which can be used in any of the other sections (for pictures of the homes, just find expensive oceanfront houses and that will be fine).

I promise to provide feedback to each and every design submission. I appreciate the hard work that all of you are putting into your designs. There can be only one contest winner, but I hope to give all of you helpful feedback to submit the best designs possible!

Target Market(s)

Very wealthy home owners of oceanfront properties. These properties are worth several millions of dollars, and thus the site and brand needs to be targeted to very wealthy, successful individuals and families (both US and international buyers).

Industry/Entity Type

Real Estate

Number of Pages Required

2 page

Requirements
Must have
• I don’t want to give too many requirements, because I want to let you all be creative. However, here are the few Must Haves:
• Must submit 2 page designs (a home page and a sub page)
• Must use logo provided
• Focus is mostly on homes, but I would like to include some beach/ocean imagery as well
• The first “item” on the home page should be an accordion/slider which shows pictures of homes and with 1 line of text: “List with the Leader” and two link buttons: “Sell Your Home” and “Buy Your Home”
• Color palette needs to be mainly blues--to match ocean and sky blue
• Exported in all major formats (psd,ai,eps,png,jpeg,etc)
Nice to have
• We don’t necessarily need all of these, but would like to feature most:
• List of videos
• “Meet the Team”—brief team bios and pics
• Link(s) to Blog
• “List with the Leader” – section on why they should choose this firm
• Featured Listings
• Previously Sold

```html
<!DOCTYPE html>
<html lang="en">
<head>
<meta charset="utf-8">
<title>Marwick on the Shore — Home</title>
<link href="https://fonts.googleapis.com/css2?family=Open+Sans:wght@300;400;600;700&display=swap" rel="stylesheet">
<style>
:root{
  --blue:#2aa6ee;
  --blue-dark:#1b8fd6;
  --ink:#2b2b2b;
  --text:#666;
  --muted:#999;
  --line:#e3e3e3;
  --footer:#2d2d2d;
  --footer-base:#222;
  --panel:#ececec;
  --white:#fff;
}
*{margin:0;padding:0;box-sizing:border-box}
html,body{width:1200px;height:3719px;overflow:hidden}
body{font-family:"Open Sans",Arial,sans-serif;color:var(--text);background:var(--white);position:relative;font-size:13px}
.abs{position:absolute}
.btn{position:absolute;display:flex;align-items:center;justify-content:center;color:var(--white);background:var(--blue);font-size:11px;font-weight:600;letter-spacing:.5px;text-transform:uppercase;text-decoration:none}

/* hero */
.hero{left:0;top:0;width:1200px;height:783px;background:linear-gradient(180deg,#6d8fa8 0%,#7f9a86 22%,#5e7a4f 40%,#8c8a78 60%,#b9ad98 78%,#8a7f70 100%)}
.topbar{left:0;top:0;width:1200px;height:30px;background:rgba(20,20,20,.75)}
.topbar .label{left:99px;top:8px;font-size:11px;color:var(--white);font-weight:600}
.topbar .dot{top:7px;width:16px;height:16px;border-radius:50%;background:#9aa3ab}
.search{left:905px;top:5px;width:198px;height:21px;border:1px solid #777;background:#1b1b1b;color:#bbb;font-size:10px;padding:3px 8px}
.brand{left:99px;top:40px;width:160px;color:var(--white);font-weight:600;font-size:20px;line-height:24px;text-transform:uppercase;letter-spacing:1px}
.arrow{top:362px;width:50px;height:50px;background:var(--blue)}
.hero-title{right:99px;top:355px;font-size:52px;font-weight:300;color:var(--white);letter-spacing:1px;white-space:nowrap}
.hero-copy{right:99px;top:425px;width:560px;text-align:right;font-size:13px;line-height:19px;color:var(--white)}
.btn-outline{left:751px;top:503px;width:169px;height:58px;border:2px solid var(--white);background:transparent;font-size:13px;font-weight:400}
.btn-download{left:932px;top:503px;width:169px;height:58px;font-size:13px;font-weight:400}
.pager{top:745px;width:9px;height:9px;border-radius:50%;background:rgba(255,255,255,.6)}

/* nav */
.nav{left:0;top:783px;width:1200px;height:104px;background:var(--blue)}
.nav ul{position:absolute;left:99px;top:0;display:flex;list-style:none;height:104px}
.nav li{color:var(--white);font-size:14px;font-weight:600;padding:0 16px;line-height:104px;white-space:nowrap}
.nav li.active{background:var(--white);color:var(--blue);width:100px;text-align:center}

/* welcome */
.map{left:200px;top:900px;width:800px;height:400px;background:radial-gradient(ellipse at center,#eef3f7 0%,#f6f9fb 60%,#fff 100%)}
.welcome-title{left:0;top:918px;width:1200px;text-align:center;font-size:31px;line-height:46px;color:#333;font-weight:400}
.welcome-copy{left:220px;top:1040px;width:760px;text-align:center;font-size:12px;line-height:17px;color:#777}
.welcome-copy p{margin-bottom:9px}

/* video */
.video-bg{left:0;top:1433px;width:1200px;height:369px;background:linear-gradient(180deg,#2e3e4f 0%,#3b4a55 45%,#5d5b52 80%,#3e3b35 100%)}
.video-kicker{left:99px;top:1487px;font-size:17px;color:var(--white);font-weight:400;letter-spacing:.5px}
.video-title{left:99px;top:1522px;font-size:60px;color:var(--white);font-weight:300;letter-spacing:1px}
.video-copy{left:99px;top:1610px;width:450px;font-size:13px;line-height:19px;color:#e6e6e6}
.player{left:580px;top:1475px;width:521px;height:290px;background:radial-gradient(ellipse at 45% 60%,#c9a24e 0%,#6a3f6a 25%,#1c2340 60%,#0c1020 100%)}
.player-bar{left:580px;top:1745px;width:521px;height:20px;background:rgba(0,0,0,.7)}

/* listings */
.section-title{left:0;top:1848px;width:1200px;text-align:center;font-size:23px;color:#222;letter-spacing:1.5px;font-weight:400}
.section-sub{left:300px;top:1897px;width:600px;text-align:center;font-size:11px;line-height:15px;color:#555}
.listing{top:1976px;width:318px}
.listing-photo{height:206px;position:relative}
.listing-price{position:absolute;right:0;bottom:36px;background:var(--blue);color:var(--white);font-size:15px;font-weight:700;padding:8px 14px}
.listing-name{margin-top:24px;text-align:center;font-size:18px;font-weight:600;color:#222;padding-bottom:10px;border-bottom:1px solid var(--line)}
.listing-meta{text-align:center;font-size:14px;color:#777;line-height:30px;margin-top:8px}
.circle{position:absolute;top:60px;width:56px;height:56px;border-radius:50%;background:var(--blue)}

/* promo */
.promo{left:99px;top:2424px;width:1002px;height:201px;box-shadow:0 1px 4px rgba(0,0,0,.15)}
.promo-panel{left:99px;top:2424px;width:404px;height:201px;background:var(--blue)}
.promo-photo{left:503px;top:2424px;width:598px;height:201px;background:linear-gradient(180deg,#6d6a7a 0%,#c98f6a 40%,#e7b27a 55%,#8b7a6d 75%,#cdb8a0 100%)}
.promo-title{left:131px;top:2440px;font-size:24px;font-weight:700;color:var(--white)}
.promo-copy{left:131px;top:2484px;width:340px;font-size:13px;line-height:18px;color:var(--white)}
.btn-quote{left:131px;top:2568px;width:129px;height:31px;background:#333;font-weight:600;font-size:10px}

/* testimonials & blog */
.col-head{top:2704px;font-size:14px;font-weight:700;color:var(--blue);text-transform:uppercase;padding-bottom:6px;border-bottom:2px solid var(--line)}
.col-head span{border-bottom:2px solid var(--blue);padding-bottom:6px}
.thumb{width:99px;height:111px}
.item-name{font-size:13px;font-weight:600;color:#222;text-transform:uppercase}
.item-copy{font-size:11px;line-height:16px;color:#777}
.item-copy a{color:var(--blue);text-decoration:none}
.sep{height:1px;background:var(--line)}
.btn-small{position:absolute;width:110px;height:22px;border:1px solid #ccc;font-size:9px;color:#555;display:flex;align-items:center;justify-content:center;text-transform:uppercase;letter-spacing:.5px}
.date{font-size:11px;color:#777}

/* contact cta */
.cta{left:99px;top:3089px;width:1002px;height:124px;background:var(--panel)}
.cta-title{left:126px;top:3113px;font-size:25px;color:#555;font-weight:400}
.cta-copy{left:126px;top:3153px;font-size:13px;color:#888}
.btn-cta{left:927px;top:3131px;width:139px;height:35px;font-weight:400}

/* footer */
.footer{left:0;top:3267px;width:1200px;height:392px;background:var(--footer)}
.foot-head{top:3300px;font-size:23px;color:var(--white);font-weight:400}
.foot-text{font-size:10.5px;line-height:19px;color:#bbb}
.links{left:355px;top:3365px;width:210px;list-style:none}
.links li{font-size:11px;color:var(--blue);height:30px;line-height:30px;border-bottom:1px solid #3d3d3d}
.tweet{font-size:10.5px;line-height:16px;color:#bbb;width:230px}
.tweet b{color:var(--blue);font-weight:400}
.field{left:870px;width:231px;height:35px;background:#363636;border:1px solid #444;color:#999;font-size:11px;padding:9px 10px}
.btn-submit{left:870px;top:3587px;width:78px;height:35px;font-size:10px}
.base{left:0;top:3659px;width:1200px;height:60px;background:var(--footer-base)}
.copyright{left:94px;top:3682px;font-size:11px;color:#999}
</style>
</head>
<body>

<!-- hero slider -->
<div class="abs hero" role="img" aria-label="Oceanfront estate courtyard with fountain, palm trees and sea view"></div>
<div class="abs topbar">
  <span class="abs label">Social Connect</span>
  <span class="abs dot" style="left:195px"></span>
  <span class="abs dot" style="left:215px"></span>
  <span class="abs dot" style="left:235px"></span>
  <span class="abs dot" style="left:255px"></span>
  <div class="abs search">Search...</div>
  <svg class="abs" style="left:1080px;top:9px" width="14" height="14" viewBox="0 0 14 14"><circle cx="5.5" cy="5.5" r="4.2" fill="none" stroke="#fff" stroke-width="1.6"/><line x1="8.6" y1="8.6" x2="13" y2="13" stroke="#fff" stroke-width="1.8"/></svg>
</div>
<div class="abs brand">Marwick<br>on the<br>Shore</div>

<div class="abs arrow" style="left:0"><svg width="50" height="50" viewBox="0 0 50 50"><polyline points="29,16 20,25 29,34" fill="none" stroke="#fff" stroke-width="3"/></svg></div>
<div class="abs arrow" style="left:1150px"><svg width="50" height="50" viewBox="0 0 50 50"><polyline points="21,16 30,25 21,34" fill="none" stroke="#fff" stroke-width="3"/></svg></div>

<h1 class="abs hero-title">LIST WITH THE LEADER</h1>
<p class="abs hero-copy">Orange County's trusted oceanfront specialists. We pair exceptional coastal homes with discerning buyers and guide every sale with care, discretion and proven market insight.</p>
<a class="btn btn-outline">Sell Your Home</a>
<a class="btn btn-download">Buy Your Home</a>
<span class="abs pager" style="left:568px"></span>
<span class="abs pager" style="left:586px;background:#fff"></span>
<span class="abs pager" style="left:604px"></span>

<!-- navigation -->
<nav class="abs nav">
  <ul>
    <li class="active">Welcome</li>
    <li>Featured Listings</li>
    <li>Previously Sold</li>
    <li>Sell</li>
    <li>Property Search</li>
    <li>Team</li>
    <li>Videos</li>
    <li>Blog</li>
    <li>Explore O.C.</li>
    <li>Contact</li>
  </ul>
</nav>

<!-- welcome -->
<div class="abs map" role="img" aria-label="Faint world map background"></div>
<h2 class="abs welcome-title">WELCOME TO<br>MARWICK ON THE SHORE</h2>
<div class="abs welcome-copy">
  <p>We envision a coastal marketplace where every oceanfront home is presented with the care it deserves, and every buyer finds the view they have been waiting for.</p>
  <p>We believe that through local knowledge, global reach and honest advice, our clients save time and make confident decisions without compromise on value or detail.</p>
  <p>We believe this standard rests on a balance of five factors<br>A carefully curated portfolio of the finest oceanfront properties along the Orange County coast</p>
  <p>Rigorous pricing built on recent sales and deep market data</p>
  <p>Seasoned agents with years of coastal experience who bring genuine passion to the neighborhoods they serve</p>
  <p>Marketing that reaches qualified buyers across the nation and the world</p>
</div>
<a class="btn" style="left:530px;top:1306px;width:139px;height:33px;font-weight:400">Read More</a>

<!-- video parallax -->
<div class="abs video-bg" role="img" aria-label="Beach at dusk with people walking along the shore"></div>
<p class="abs video-kicker">BACKGROUND PARALLAX WITH</p>
<h2 class="abs video-title">ANY VIDEO</h2>
<p class="abs video-copy">Lorem ipsum dolor sit amet, consectetur adipisicing elit, sed do eius-mod tempor incididunt ut labore et dolore magna aliqua. Ut enim ad minim veniam, quis nostrud exercitation ullamco laboris nisi ut aliquip ex ea commodo consequat.</p>
<div class="abs player" role="img" aria-label="Aerial evening view of the coastline in a video player"></div>
<div class="abs player-bar">
  <svg class="abs" style="left:8px;top:5px" width="10" height="10" viewBox="0 0 10 10"><polygon points="1,0 9,5 1,10" fill="#fff"/></svg>
  <div class="abs" style="left:28px;top:9px;width:400px;height:2px;background:#666"></div>
</div>
<svg class="abs" style="left:1081px;top:1485px" width="12" height="44" viewBox="0 0 12 44"><path d="M6 9 L1 4 A2.5 2.5 0 0 1 6 2 A2.5 2.5 0 0 1 11 4 Z" fill="#fff"/><circle cx="6" cy="22" r="4.5" fill="none" stroke="#fff" stroke-width="1.4"/><polygon points="1,40 11,35 7,44" fill="#fff"/></svg>

<!-- featured listings -->
<h2 class="abs section-title">FEATURED OCEANFRONT LISTINGS</h2>
<p class="abs section-sub">Contrary to popular belief, Lorem Ipsum is not simply random text. It has roots in a piece of classical Latin literature from 45 BC, making it over 2000 years old. Howard Pellman, a Latin professor at Westbrook College in Ohio.</p>

<div class="abs listing" style="left:99px">
  <div class="listing-photo" role="img" aria-label="Beach cottage row at dusk" style="background:linear-gradient(180deg,#16204a 0%,#2b3d7a 45%,#c7a46a 75%,#d9c49a 100%)"><span class="listing-price">FROM $2.4M</span></div>
  <h3 class="listing-name">BEACHFRONT COTTAGE</h3>
  <div class="listing-meta">Beds: 3 Bedrooms, 2 Baths<br>Lot size: 4,200 sq ft</div>
</div>

<div class="abs listing" style="left:441px">
  <div class="listing-photo" role="img" aria-label="Oceanfront villa under a blue sky" style="background:linear-gradient(180deg,#6f98c4 0%,#a9c3dd 45%,#c48f62 70%,#d9c3a3 100%)">
    <span class="circle" style="left:96px"><svg width="56" height="56" viewBox="0 0 56 56"><circle cx="26" cy="26" r="8" fill="none" stroke="#fff" stroke-width="2.5"/><line x1="32" y1="32" x2="38" y2="38" stroke="#fff" stroke-width="3"/></svg></span>
    <span class="circle" style="left:166px"><svg width="56" height="56" viewBox="0 0 56 56"><rect x="18" y="19" width="20" height="18" rx="2" fill="none" stroke="#fff" stroke-width="2"/><line x1="18" y1="24" x2="38" y2="24" stroke="#fff" stroke-width="2"/><line x1="23" y1="16" x2="23" y2="21" stroke="#fff" stroke-width="2"/><line x1="33" y1="16" x2="33" y2="21" stroke="#fff" stroke-width="2"/></svg></span>
  </div>
  <h3 class="listing-name">MEDITERRANEAN VILLA</h3>
  <div class="listing-meta">Beds: 5 Bedrooms, 4 Baths<br>Lot size: 9,800 sq ft</div>
</div>

<div class="abs listing" style="left:783px">
  <div class="listing-photo" role="img" aria-label="Estate pool with palm trees by the sea" style="background:linear-gradient(180deg,#4f8fcf 0%,#8fbde6 40%,#3f6b4a 65%,#7aa9c2 100%)"><span class="listing-price">FROM $6.9M</span></div>
  <h3 class="listing-name">CLIFFTOP ESTATE</h3>
  <div class="listing-meta">Beds: 6 Bedrooms, 5 Baths<br>Lot size: 14,500 sq ft</div>
</div>
<a class="btn" style="left:530px;top:2355px;width:139px;height:31px;font-weight:400">View All</a>

<!-- promo -->
<div class="abs promo"></div>
<div class="abs promo-panel"></div>
<div class="abs promo-photo" role="img" aria-label="Sunset over the beach with a person at the waterline"></div>
<h3 class="abs promo-title">Thinking of selling?</h3>
<p class="abs promo-copy">Contact us for a private valuation of your oceanfront home.</p>
<a class="btn btn-quote">Get a Quote</a>

<!-- testimonials -->
<div class="abs col-head" style="left:99px;width:486px"><span>Testimonials</span></div>
<div class="abs thumb" style="left:99px;top:2752px;background:linear-gradient(180deg,#cfdbe6,#7d9ab5)" role="img" aria-label="Portrait of a client in a blue shirt"></div>
<div class="abs" style="left:216px;top:2752px;width:369px">
  <p class="item-name">Alan Carver</p>
  <p class="item-copy" style="margin-top:8px">Lorem ipsum dolor sit amet, consectetur adipiscing elit. Quisque quis orci sed elit ultrices aliquam vel sit amet dolor. Suspendisse potenti. Cras a ipsum tellus. Nulla placerat ligula nec massa hendrerit, in pretium mi <a>Read More</a></p>
</div>
<div class="abs sep" style="left:99px;top:2876px;width:486px"></div>
<div class="abs thumb" style="left:99px;top:2888px;background:linear-gradient(180deg,#d8d2c8,#6e6a66)" role="img" aria-label="Portrait of a client in a dark suit"></div>
<div class="abs" style="left:216px;top:2888px;width:369px">
  <p class="item-name">Mark Ellison</p>
  <p class="item-copy" style="margin-top:8px">Aliquam feugiat orci nunc, vel fringilla ligula tempus eget. Pellentesque habitant morbi tristique senectus et netus et malesuada fames ac turpis egestas. Mauris eu nisl egestas, bibendum orci vel, tempus libero. Cras quis lacus <a>Read More</a></p>
</div>

<!-- blog -->
<div class="abs col-head" style="left:612px;width:489px"><span>Recent Blog Posts</span></div>
<div class="abs" style="left:612px;top:2752px;width:107px;height:87px;background:linear-gradient(180deg,#e8e6e2,#9c958c)" role="img" aria-label="Bright living room interior"></div>
<div class="abs" style="left:739px;top:2752px;width:362px">
  <p class="item-name" style="text-transform:none">3 Bedroom Condo!</p>
  <p class="item-copy" style="margin-top:6px">Lorem ipsum dolor sit amet, consectetur adipiscing elit. Nullam ultricies justo sit amet turpis mollis, quis ultrices...</p>
</div>
<span class="abs date" style="left:1020px;top:2827px">October 16, 2014</span>
<span class="btn-small" style="left:739px;top:2822px">Read More</span>
<div class="abs sep" style="left:612px;top:2865px;width:489px"></div>
<div class="abs" style="left:612px;top:2888px;width:107px;height:87px;background:linear-gradient(180deg,#d6d3cf,#8a8279)" role="img" aria-label="Modern dining room interior"></div>
<div class="abs" style="left:739px;top:2888px;width:362px">
  <p class="item-name" style="text-transform:none">Open House Tonight</p>
  <p class="item-copy" style="margin-top:6px">Lorem ipsum dolor sit amet, consectetur adipiscing elit. Morbi vehicula dapibus mauris, quis ullamcorper enim aliquet eget nec...</p>
</div>
<span class="abs date" style="left:1040px;top:2963px">June 3, 2014</span>
<span class="btn-small" style="left:739px;top:2958px">Read More</span>

<!-- contact cta -->
<div class="abs cta"></div>
<h3 class="abs cta-title">Contact Us to Sign Up for an Open House</h3>
<p class="abs cta-copy">Lorem ipsum dolor sit amet, consectetur adipiscing elit. Morbi vehicula dapibus mauris.</p>
<a class="btn btn-cta">View All</a>

<!-- footer -->
<footer class="abs footer"></footer>
<h4 class="abs foot-head" style="left:94px">Contact</h4>
<h4 class="abs foot-head" style="left:355px">Quick Links</h4>
<h4 class="abs foot-head" style="left:610px">Latest Tweets</h4>
<h4 class="abs foot-head" style="left:870px">Contact Us</h4>

<div class="abs foot-text" style="left:94px;top:3360px;width:240px">
  <p>Harlow Coastal Holdings LLC</p><br>
  <p>(Seaside Office / Head Office)<br>Suite 410, 88 Tidewater Lane,<br>Laguna Point, CA 92600<br>Phone: (555) 014 2207</p>
  <p>(Harbor Office)<br>Unit 2, 15 Harbor Crest Road,<br>Seabrook, CA 92601<br>(555) 019 3381</p>
</div>

<ul class="abs links">
  <li>» Lorem ipsum dolor sit</li>
  <li>» Amet consectetur</li>
  <li>» Praesent vel sem id</li>
  <li>» Curabitur hendrerit est</li>
  <li>» Aliquam eget erat nec sapien</li>
  <li>» Cras id augue nunc</li>
  <li>» Sed a nulla urna</li>
</ul>

<p class="abs tweet" style="left:610px;top:3366px"><b>@marwickshore</b> Justo nonummy laoreet phasellent penatoque in antequae pellus elis eget tincidunt. Nequeduis laoreet justo a non tellus laoreet vitae doloreet<br>1 day ago</p>
<p class="abs tweet" style="left:610px;top:3470px"><b>@marwickshore</b> Justo nonummy laoreet phasellent penatoque in antequae pellus elis eget tincidunt. Nequeduis laoreet justo a non tellus laoreet vitae doloreet<br>1 day ago</p>

<div class="abs field" style="top:3357px">Full Name</div>
<div class="abs field" style="top:3402px">Email Address</div>
<div class="abs field" style="top:3447px">Subject</div>
<div class="abs field" style="top:3492px;height:78px">Message</div>
<a class="btn btn-submit">Submit</a>

<div class="abs base"></div>
<p class="abs copyright">Copyright © 2015 marwickontheshore.example - All Rights Reserved</p>

</body>
</html>
```